Looking for a modern, Professional business card design

We have a simple business card, but are looking for a more modern, professional look. A sample of the basic card is attached as well as the logo. We would also like to add that we offer:
Struggling with your finances?
- Learn to become debt free
- Discover the power of cash
- Control your money instead of it controlling you
Let us help you achieve a new level of financial freedom!
Also, we would like to have a "SPECIAL OFFER!: FREE 30 minute consultation"
Financial Planning

```html
<!DOCTYPE html>
<html lang="en">
<head>
<meta charset="utf-8">
<title>Northway Coaching – Business Card</title>
<link rel="stylesheet" href="https://fonts.googleapis.com/css2?family=Roboto:wght@400;500;700;900&family=Roboto+Condensed:wght@700&display=swap">
<style>
  :root {
    --backdrop: #8f8f8f;
    --card-white: #f1f1f4;
    --ink: #1b1b1b;
    --ink-soft: #4a4a4a;
    --brand-green: #2a8c3f;
    --back-green: #279042;
    --light-green: #8cc63f;
    --faint-lilac: #dcdce8;
    --paper-text: #ececec;
  }
  * { margin: 0; padding: 0; box-sizing: border-box; }
  html, body { width: 1105px; height: 1200px; overflow: hidden; }
  body {
    background: var(--backdrop);
    font-family: "Roboto", Arial, sans-serif;
    position: relative;
  }
  .card {
    position: absolute;
    left: 182px;
    width: 746px;
    height: 427px;
    overflow: hidden;
  }
  .card--front { top: 119px; background: var(--card-white); }
  .card--back { top: 637px; background: var(--back-green); color: var(--paper-text); }

  /* Front */
  .front__accent {
    position: absolute; right: 60px; top: 20px;
    width: 96px; height: 96px; border-radius: 50%;
    background: var(--faint-lilac);
  }
  .brand {
    position: absolute; left: 44px; top: 98px;
    display: flex; align-items: center; gap: 16px;
  }
  .brand__dot {
    width: 40px; height: 40px; border-radius: 50%;
    background: var(--light-green);
  }
  .brand__name {
    font-weight: 900; font-size: 50px; letter-spacing: 1px;
    color: var(--ink); line-height: 1;
  }
  .brand__tagline {
    position: absolute; left: 248px; top: 156px;
    font-size: 13px; color: var(--ink-soft);
  }
  .person { position: absolute; left: 246px; top: 222px; }
  .person__name {
    font-weight: 500; font-size: 28px; color: var(--brand-green);
    letter-spacing: 0.5px; line-height: 1.1;
  }
  .person__title { font-size: 20px; color: var(--ink); margin-top: 4px; }
  .contact {
    position: absolute; left: 246px; top: 298px;
    list-style: none;
  }
  .contact__item {
    display: flex; align-items: center; gap: 10px;
    font-size: 19.5px; color: var(--ink-soft); height: 29px;
  }
  .contact__icon { width: 18px; height: 18px; flex: none; }

  /* Back */
  .back__accent {
    position: absolute; left: 628px; top: 12px;
    width: 100px; height: 100px; border-radius: 50%;
    background: var(--light-green);
  }
  .pitch { position: absolute; left: 63px; top: 74px; }
  .pitch__question { font-weight: 500; font-size: 21px; letter-spacing: 0.3px; }
  .pitch__list { list-style: none; margin-top: 12px; }
  .pitch__list li { font-size: 19.5px; line-height: 31.5px; }
  .pitch__list li::before { content: "•"; margin-right: 12px; }
  .pitch__promise {
    font-family: "Roboto Condensed", Arial, sans-serif;
    font-weight: 700; font-size: 19px; margin-top: 14px;
  }
  .offer { position: absolute; left: 63px; top: 256px; }
  .offer__headline { font-weight: 900; font-size: 49px; line-height: 1; letter-spacing: 0.5px; }
  .offer__detail { font-weight: 900; font-size: 25px; margin-top: 10px; letter-spacing: 0.3px; }
</style>
</head>
<body>
  <section class="card card--front" aria-label="Card front">
    <div class="front__accent"></div>
    <div class="brand">
      <span class="brand__dot"></span>
      <span class="brand__name">NORTHWAY COACHING</span>
    </div>
    <p class="brand__tagline">Achieve a new level of personal freedom</p>
    <div class="person">
      <p class="person__name">DANIEL R. HAYES</p>
      <p class="person__title">Personal Financial Coach</p>
    </div>
    <ul class="contact">
      <li class="contact__item">
        <svg class="contact__icon" viewBox="0 0 18 18" aria-hidden="true"><rect x="4" y="1" width="10" height="16" rx="2" fill="none" stroke="#2a8c3f" stroke-width="2"/><circle cx="9" cy="14" r="1" fill="#2a8c3f"/></svg>
        (205) 555-0142
      </li>
      <li class="contact__item">
        <svg class="contact__icon" viewBox="0 0 18 18" aria-hidden="true"><rect x="1" y="4" width="16" height="11" fill="#2a8c3f"/><path d="M1 4 L9 10 L17 4" fill="none" stroke="#f1f1f4" stroke-width="1.5"/></svg>
        daniel@northwaycoaching.com
      </li>
      <li class="contact__item">
        <svg class="contact__icon" viewBox="0 0 18 18" aria-hidden="true"><circle cx="9" cy="9" r="8" fill="#2a8c3f"/><path d="M1 9 H17 M9 1 C5 5 5 13 9 17 M9 1 C13 5 13 13 9 17" fill="none" stroke="#f1f1f4" stroke-width="1.2"/></svg>
        www.northwaycoaching.com
      </li>
    </ul>
  </section>

  <section class="card card--back" aria-label="Card back">
    <div class="back__accent"></div>
    <div class="pitch">
      <p class="pitch__question">STRUGGLING WITH YOUR FINANCES?</p>
      <ul class="pitch__list">
        <li>Learn to become debt free</li>
        <li>Discover the power of cash</li>
        <li>Control your money instead of it controlling you</li>
      </ul>
      <p class="pitch__promise">Let us help you achieve a new level of financial freedom!</p>
    </div>
    <div class="offer">
      <p class="offer__headline">SPECIAL OFFER!</p>
      <p class="offer__detail">FREE 30 MINUTE CONSULTATION</p>
    </div>
  </section>
</body>
</html>
```